Brell Stone Company Business Cards

Front and Back Business Card - logo and text setup - cool design. I need workable photoshop or illustrator files so I can setup each employee card with design that is created
Updates

Hi everyone, thank you for the great entries. Please no more white and blue cards - there are so many already - black and silver only now please. thanks!

Target Market(s)

Construction Industry - Facility Managers

Industry/Entity Type

Construction

Contact Information for Business Card

I really like contemporary simplistic looks - clean neat....not opposed to seeing some black backrounds

Requirements
Must have
• Logo/website address with design on front only - www.brellstone-example.com (logo attached)
• Back:
• Name/Title/Company Address/Phone/email address
Nice to have
• Cool design
Should not have
• Nothing gimmicky like Fire or Water - since we are a Fire Protection company - it has all been done

```html
<!DOCTYPE html>
<html lang="en">
<head>
<meta charset="utf-8">
<title>Brell Stone Company – Business Cards</title>
<link rel="stylesheet" href="https://fonts.googleapis.com/css2?family=Lato:wght@400;700;900&display=swap">
<style>
  :root {
    --black: #151515;
    --charcoal: #2a2a2c;
    --silver: #b9bcc2;
    --silver-light: #d9dbdf;
    --white: #ffffff;
    --ink: #1c1c1c;
    --backdrop: #e4e5e9;
  }
  * { margin: 0; padding: 0; box-sizing: border-box; }
  html, body {
    width: 1200px;
    height: 900px;
    overflow: hidden;
    background: var(--backdrop);
    font-family: "Lato", Arial, sans-serif;
  }
  .canvas {
    position: relative;
    width: 1200px;
    height: 900px;
  }
  .card {
    position: absolute;
    left: 260px;
    width: 680px;
    height: 388px;
    overflow: hidden;
    box-shadow: 0 6px 18px rgba(0,0,0,0.22);
  }

  /* Logo side */
  .card--logo-side {
    top: 40px;
    background: var(--black);
    color: var(--silver-light);
  }
  .card--logo-side .wordmark {
    position: absolute;
    top: 120px;
    left: 0;
    width: 100%;
    text-align: center;
    font-weight: 900;
    font-size: 74px;
    line-height: 1;
    letter-spacing: -1px;
    color: var(--silver-light);
  }
  .card--logo-side .website {
    position: absolute;
    top: 262px;
    width: 100%;
    text-align: center;
    font-size: 20px;
    letter-spacing: 0.5px;
    color: var(--silver);
  }

  /* Contact side */
  .card--contact-side {
    top: 464px;
    background: var(--white);
    color: var(--ink);
  }
  .card--contact-side .wordmark {
    position: absolute;
    top: 28px;
    left: 38px;
    font-weight: 900;
    font-size: 58px;
    line-height: 1;
    letter-spacing: -1px;
    color: var(--black);
  }
  .contact {
    position: absolute;
    top: 118px;
    left: 40px;
    font-size: 17px;
    line-height: 1.35;
  }
  .contact .address { margin-bottom: 10px; }
  .contact .line {
    display: flex;
    align-items: center;
    gap: 8px;
  }
  .contact .icon { width: 14px; height: 14px; flex: none; }
  .person {
    position: absolute;
    top: 178px;
    right: 50px;
    text-align: right;
  }
  .person .name {
    font-weight: 700;
    font-size: 30px;
    color: var(--black);
  }
  .person .title {
    font-size: 20px;
    color: var(--charcoal);
    margin-top: 2px;
  }
  .footer-band {
    position: absolute;
    left: 0;
    bottom: 0;
    width: 680px;
    height: 388px;
  }
  .card--contact-side .website {
    position: absolute;
    bottom: 16px;
    right: 70px;
    font-size: 21px;
    color: var(--silver-light);
    letter-spacing: 0.5px;
  }
</style>
</head>
<body>
<main class="canvas">

  <section class="card card--logo-side" aria-label="Card logo side">
    <div class="wordmark">Brell Stone</div>
    <div class="website">www.brellstone-example.com</div>
  </section>

  <section class="card card--contact-side" aria-label="Card contact side">
    <svg class="footer-band" viewBox="0 0 680 388" aria-hidden="true">
      <path d="M30,270 C230,318 470,332 680,300 L680,318 C470,346 230,330 30,270 Z" fill="var(--silver)"/>
      <path d="M0,270 C200,318 460,345 680,326 L680,388 L0,388 Z" fill="var(--black)"/>
    </svg>

    <div class="wordmark">Brell Stone</div>

    <div class="contact">
      <div class="address">48-2 Harbor Point Road<br>Northfield, NY 11890</div>
      <div class="line">
        <svg class="icon" viewBox="0 0 24 24" aria-hidden="true"><path fill="var(--black)" d="M6.6 10.8a15.1 15.1 0 0 0 6.6 6.6l2.2-2.2c.3-.3.7-.4 1-.2 1.1.4 2.3.6 3.6.6.6 0 1 .4 1 1V20c0 .6-.4 1-1 1A17 17 0 0 1 3 4c0-.6.4-1 1-1h3.5c.6 0 1 .4 1 1 0 1.3.2 2.5.6 3.6.1.3 0 .7-.2 1z"/></svg>
        <span>(555) 214-0387</span>
      </div>
      <div class="line">
        <svg class="icon" viewBox="0 0 24 24" aria-hidden="true"><rect x="2" y="5" width="20" height="14" rx="1" fill="var(--black)"/><path d="M2 6l10 7 10-7" stroke="var(--white)" stroke-width="1.6" fill="none"/></svg>
        <span>info@brellstone-example.com</span>
      </div>
    </div>

    <div class="person">
      <div class="name">Dana Whitfield Marsh</div>
      <div class="title">President</div>
    </div>

    <div class="website">www.brellstone-example.com</div>
  </section>

</main>
</body>
</html>
```